TK Stationery - Modern Contemporary

Develop modern template for Letterhead and Stationery (business card, letterhead, envelopes) using the TK Logo and Icon

Colors
0054AA
0677BA
7BADD7
CADEEF
E8F1F8
00AB8E
00BBA5
67D7C9
C6EFE9
E9F9F6
EE7325
F08F49
F5BC92
FAE3D3
FDF4ED
6B429C
8869AF
B7A5CE
E3DAEB
F3F0F8

```html
<!DOCTYPE html>
<html lang="en">
<head>
<meta charset="utf-8">
<title>Tavi Kora Business Card</title>
<link rel="stylesheet" href="https://fonts.googleapis.com/css2?family=Oswald:wght@600&family=Open+Sans:wght@400;600&display=swap">
<style>
  :root {
    --stage: #bdbdbd;
    --card: #2a2f4b;
    --green: #1db57a;
    --orange: #ee7325;
    --text: #ffffff;
    --rule: #d9dbe6;
  }
  * { box-sizing: border-box; margin: 0; padding: 0; }
  html, body { width: 1200px; height: 800px; overflow: hidden; }
  body {
    background: var(--stage);
    display: flex;
    align-items: center;
    justify-content: center;
    gap: 60px;
    font-family: "Open Sans", Arial, sans-serif;
  }
  .card {
    width: 525px;
    height: 300px;
    background: var(--card);
    border-bottom: 4px solid var(--green);
    position: relative;
    box-shadow: 0 8px 24px rgba(0,0,0,0.25);
  }
  .card-front {
    display: flex;
    align-items: center;
    padding: 0 40px 0 56px;
  }
  .identity { width: 200px; text-align: right; padding-right: 22px; }
  .identity-name {
    font-family: "Oswald", Arial, sans-serif;
    font-weight: 600;
    font-size: 30px;
    color: var(--green);
    line-height: 1.1;
    letter-spacing: 0.3px;
  }
  .identity-title {
    font-size: 14px;
    color: var(--orange);
    margin-top: 2px;
  }
  .divider {
    width: 1px;
    height: 108px;
    background: var(--rule);
  }
  .contact { list-style: none; padding-left: 22px; }
  .contact-item {
    display: flex;
    align-items: flex-start;
    gap: 10px;
    color: var(--text);
    font-size: 13px;
    line-height: 1.35;
  }
  .contact-item + .contact-item { margin-top: 3px; }
  .contact-item.address { margin-bottom: 10px; }
  .contact-icon { width: 13px; height: 13px; flex: none; margin-top: 2px; }
  .card-back {
    display: flex;
    align-items: center;
    justify-content: center;
  }
  .wordmark {
    display: flex;
    align-items: center;
    gap: 12px;
    font-family: "Open Sans", Arial, sans-serif;
    font-weight: 600;
    font-size: 60px;
    color: var(--green);
    letter-spacing: 1px;
  }
  .wordmark-dot {
    width: 14px;
    height: 14px;
    border-radius: 50%;
    background: var(--orange);
  }
</style>
</head>
<body>
  <section class="card card-front">
    <div class="identity">
      <p class="identity-name">Daniel Reyes</p>
      <p class="identity-title">President</p>
    </div>
    <div class="divider"></div>
    <ul class="contact">
      <li class="contact-item address">
        <svg class="contact-icon" viewBox="0 0 16 16"><path d="M8 1a5 5 0 0 0-5 5c0 4 5 9 5 9s5-5 5-9a5 5 0 0 0-5-5z" fill="#1db57a"/><circle cx="8" cy="6" r="2" fill="#2a2f4b"/></svg>
        <span>4120 Alder Court<br>Fairbanks, Alaska 99701</span>
      </li>
      <li class="contact-item">
        <svg class="contact-icon" viewBox="0 0 16 16"><path d="M4 1l3 3-2 2c1 2 3 4 5 5l2-2 3 3-2 3C7 15 1 9 1 3z" fill="#1db57a"/></svg>
        <span>555-014-2290</span>
      </li>
      <li class="contact-item">
        <svg class="contact-icon" viewBox="0 0 16 16"><rect x="4" y="1" width="8" height="14" rx="1.5" fill="none" stroke="#1db57a" stroke-width="1.6"/><circle cx="8" cy="12.5" r="0.9" fill="#1db57a"/></svg>
        <span>555-018-7731</span>
      </li>
      <li class="contact-item">
        <svg class="contact-icon" viewBox="0 0 16 16"><rect x="1" y="3" width="14" height="10" rx="1" fill="#1db57a"/><path d="M1.5 3.5L8 9l6.5-5.5" fill="none" stroke="#2a2f4b" stroke-width="1.4"/></svg>
        <span>hello@tavikora.com</span>
      </li>
      <li class="contact-item">
        <svg class="contact-icon" viewBox="0 0 16 16"><circle cx="8" cy="8" r="6.5" fill="none" stroke="#1db57a" stroke-width="1.5"/><path d="M1.5 8h13M8 1.5c-3 3.5-3 9.5 0 13M8 1.5c3 3.5 3 9.5 0 13" fill="none" stroke="#1db57a" stroke-width="1.2"/></svg>
        <span>tavikora.com</span>
      </li>
    </ul>
  </section>

  <section class="card card-back">
    <div class="wordmark">
      <span class="wordmark-name">tavi kora</span>
      <span class="wordmark-dot"></span>
    </div>
  </section>
</body>
</html>
```